Business Card for Coastal Tundrabridge Advisory

We need a business card for Coastal Tundrabridge Advisory. The company website address is provided below. The company logo is attached. We provide specialized permafrost services to the mining, transportation, and oil & gas industries. The card should be prepared for:
Matthias Korhonen, PhD.
Coastal Tundrabridge Advisory
PO Box 418259
Quillwater, Alaska 99642
Direct: +1-907-555-0143
Email: mkorhonen@tundrabridgeadvisory.example
Website: www.coastaltundrabridgeadvisory.example

```html
<!DOCTYPE html>
<html lang="en">
<head>
<meta charset="utf-8">
<title>Coastal Tundrabridge Advisory – Business Card</title>
<link href="https://fonts.googleapis.com/css2?family=Roboto:wght@300;400;500;700&display=swap" rel="stylesheet">
<style>
  :root {
    --backdrop: #222222;
    --card: #111824;
    --ink: #ffffff;
    --ink-soft: #d9dde3;
    --ice: #3aa6dc;
    --ice-deep: #1d5f86;
    --rule: #7d8590;
  }
  * { margin: 0; padding: 0; box-sizing: border-box; }
  html, body { width: 1200px; height: 711px; overflow: hidden; background: var(--backdrop); }
  body { font-family: 'Roboto', sans-serif; color: var(--ink); position: relative; }

  .card {
    position: absolute;
    top: 195px;
    width: 560px;
    height: 320px;
    background: var(--card);
    border-radius: 22px;
    overflow: hidden;
    box-shadow: 0 14px 30px rgba(0,0,0,.55);
  }
  .card--front { left: 25px; }
  .card--back { left: 615px; }

  /* front */
  .pattern-field {
    position: absolute; inset: 0;
    background: linear-gradient(200deg, var(--ice) 0%, var(--ice-deep) 30%, rgba(17,24,36,0.6) 55%, var(--card) 80%);
    opacity: .55;
  }
  .front-brand {
    position: absolute; left: 0; right: 0; top: 112px;
    text-align: center;
  }
  .wordmark {
    font-weight: 500;
    color: var(--ink);
    letter-spacing: 1px;
  }
  .front-brand .wordmark { font-size: 30px; }
  .services {
    position: absolute; left: 0; right: 0; bottom: 30px;
    text-align: center;
  }
  .services__title { font-size: 11px; font-weight: 500; letter-spacing: .5px; margin-bottom: 4px; }
  .services__text { font-size: 11px; font-weight: 400; color: var(--ink-soft); }

  /* back */
  .back-brand {
    position: absolute; left: 28px; top: 190px; width: 230px;
  }
  .back-brand .wordmark { font-size: 21px; line-height: 1.25; }
  .divider {
    position: absolute; left: 275px; top: 70px; width: 1px; height: 190px;
    background: var(--rule);
  }
  .contact { position: absolute; left: 300px; top: 72px; right: 18px; }
  .contact__name { font-size: 24px; line-height: 1.1; }
  .contact__given { font-weight: 700; }
  .contact__family { font-weight: 300; }
  .contact__degree { font-size: 15px; font-weight: 700; margin-top: 2px; }
  .contact__address { font-size: 11px; font-weight: 400; color: var(--ink-soft); margin-top: 14px; line-height: 1.45; }
  .contact__list { list-style: none; margin-top: 16px; font-size: 10px; color: var(--ink-soft); }
  .contact__list li { display: flex; align-items: center; gap: 7px; margin-bottom: 6px; white-space: nowrap; }
  .contact__list svg { width: 11px; height: 11px; flex: none; }
</style>
</head>
<body>

<section class="card card--front" aria-label="Card front">
  <div class="pattern-field" role="img" aria-label="Repeated company name pattern fading from bright blue to dark navy"></div>
  <div class="front-brand">
    <div class="wordmark">Coastal Tundrabridge Advisory</div>
  </div>
  <div class="services">
    <p class="services__title">OUR SERVICES</p>
    <p class="services__text">We provide specialized permafrost services to the mining, transportation, and oil &amp; gas industries</p>
  </div>
</section>

<section class="card card--back" aria-label="Card back">
  <div class="back-brand">
    <div class="wordmark">Coastal Tundrabridge Advisory</div>
  </div>
  <div class="divider"></div>
  <div class="contact">
    <p class="contact__name"><span class="contact__given">Matthias</span> <span class="contact__family">Korhonen</span></p>
    <p class="contact__degree">PhD</p>
    <p class="contact__address">PO Box 418259<br>Quillwater, Alaska 99642</p>
    <ul class="contact__list">
      <li>
        <svg viewBox="0 0 24 24" aria-hidden="true"><path fill="#fff" d="M6.6 10.8a15.1 15.1 0 0 0 6.6 6.6l2.2-2.2c.3-.3.7-.4 1-.2 1.1.4 2.3.6 3.6.6.6 0 1 .4 1 1V20c0 .6-.4 1-1 1A17 17 0 0 1 3 4c0-.6.4-1 1-1h3.5c.6 0 1 .4 1 1 0 1.3.2 2.5.6 3.6.1.3 0 .7-.2 1z"/></svg>
        +1-907-555-0143
      </li>
      <li>
        <svg viewBox="0 0 24 24" aria-hidden="true"><rect x="2" y="5" width="20" height="14" rx="2" fill="none" stroke="#fff" stroke-width="2"/><path d="M2 6l10 7 10-7" fill="none" stroke="#fff" stroke-width="2"/></svg>
        mkorhonen@tundrabridgeadvisory.example
      </li>
      <li>
        <svg viewBox="0 0 24 24" aria-hidden="true"><circle cx="12" cy="12" r="10" fill="none" stroke="#fff" stroke-width="2"/><path d="M2 12h20M12 2c3 3 3 17 0 20M12 2c-3 3-3 17 0 20" fill="none" stroke="#fff" stroke-width="1.6"/></svg>
        www.coastaltundrabridgeadvisory.example
      </li>
    </ul>
  </div>
</section>

</body>
</html>
```